Lotus Ridge Website

We need a website that has clean, asian looking images that relax and motivate people to come into our integrated medical center. My current website is www.needlecalmharbor.com and I would like the design for Lotus Ridge Wellness Partners to be similar but more inviting with video content and a product purchase store as well. A moving banner would be nice too. When people are looking for ways of losing weight or getting out of pain we want them to make the connection that we have the solution. This website needs to provide sufficient information so that patients are well informed and choose us as their health provider before they ever walk through our doors. We offer comprehensive natural medicine that is based on the principles that the body can heal itself when given the right conditions. Our services include medical weight loss and hormone balancing, acupuncture and chinese herbal medicine, physical medicine, trigger point injections, allergy testing and joint rehabilitation. The Medical Doctor and Licensed Acupuncturist work as a team to provide optimal care that is catered to each individual who comes through our doors.
Updates

Target Market(s)

40 to 50 year olds who want to lose weight or have pain issues.

Industry/Entity Type

Medical

Requirements
Must have
• Use photos from our website www.needlecalmharbor.com or similar content. Video content. Moving banner with relaxing images.
Nice to have
• Happy, healthy looking people. Medical Doctors working as a team. Friendly staff in a cutting edge facility.
Should not have
• Papyrus font, or big bold words.

```html
<!DOCTYPE html>
<html lang="en">
<head>
<meta charset="utf-8">
<title>Lotus Ridge Website</title>
<link href="https://fonts.googleapis.com/css2?family=PT+Sans&family=Questrial&family=Arimo:wght@400;700&display=swap" rel="stylesheet">
<style>
:root{
  --page-top:#b6bac9;
  --page-bottom:#27303b;
  --header-top:#8587bd;
  --header-bottom:#abadd6;
  --olive:#67662a;
  --olive-text:#5a5a25;
  --menu-bg:#cdcdb8;
  --menu-line:#ffffff;
  --frame:#c9c9b9;
  --blue:#1b86c7;
  --green:#86c486;
  --body-text:#222222;
  --footer-top:#4b4b4b;
  --footer-bottom:#111111;
  --footer-link:#d8d8d8;
  --copy:#f2e96a;
  --white:#ffffff;
}
*{margin:0;padding:0;box-sizing:border-box}
html,body{width:1182px;height:1200px;overflow:hidden}
body{background:linear-gradient(var(--page-top),#6c7585 55%,var(--page-bottom));font-family:Arimo,Arial,sans-serif;position:relative}
.page{position:absolute;left:75px;top:9px;width:1039px;height:1191px;background:var(--white)}
.header{position:absolute;left:0;top:0;width:100%;height:128px;background:linear-gradient(var(--header-top),var(--header-bottom))}
.brand{position:absolute;left:26px;top:22px;display:flex;align-items:center;gap:14px}
.brand-mark{width:66px;height:66px;background:var(--olive)}
.brand-name{font-family:Questrial,sans-serif;font-size:44px;color:var(--olive-text);letter-spacing:1px}
.phones{position:absolute;right:44px;top:36px;text-align:right;font-family:Questrial,sans-serif;color:var(--white);font-size:28px;line-height:36px}
.nav{position:absolute;left:0;top:136px;width:100%;display:flex;justify-content:center;font-family:Questrial,sans-serif;font-size:18px;color:var(--olive-text)}
.nav span{padding:9px 13px;height:40px}
.nav .sep{padding:9px 0;color:var(--olive-text)}
.nav .active{background:var(--olive);color:var(--white)}
.banner{position:absolute;left:55px;top:176px;width:929px;height:413px;border:5px solid var(--frame);background:linear-gradient(100deg,#8b8f92 0%,#b3442f 30%,#54606a 50%,#a39170 70%,#e0c35a 100%)}
.arrow{position:absolute;top:336px;width:46px;height:62px;background:#a5a58f}
.arrow.left{left:15px;border-radius:31px 0 0 31px}
.arrow.right{left:984px;border-radius:0 31px 31px 0}
.arrow svg{position:absolute;top:16px}
.dropdown{position:absolute;left:428px;top:176px;width:235px;background:var(--menu-bg);font-family:Questrial,sans-serif;font-size:14.5px;color:var(--olive-text)}
.dropdown li{list-style:none;height:34.6px;line-height:34px;padding-left:17px;border-bottom:1px solid var(--menu-line)}
.intro-title,.cat-title{position:absolute;top:614px;font-family:"PT Sans",sans-serif;font-weight:400;font-size:33px;line-height:40px;color:var(--blue);white-space:nowrap}
.intro-title{left:58px}
.cat-title{left:696px;font-size:32px}
.rule{position:absolute;height:3px;background:var(--frame)}
.divider{position:absolute;left:671px;top:608px;width:1px;height:355px;background:var(--frame)}
.intro-photo{position:absolute;left:46px;top:683px;width:181px;height:248px;background:linear-gradient(#f2ede6,#e6d8c8 50%,#9aa0a6)}
.intro-text{position:absolute;left:235px;top:702px;width:403px;font-size:14.8px;line-height:18px;color:var(--body-text);text-align:justify}
.intro-text p{margin-bottom:18px}
.read-more{position:absolute;left:562px;top:930px;font-size:15px;font-weight:700;letter-spacing:1px;color:var(--body-text)}
.cat{position:absolute;left:692px;width:300px}
.cat-photo{position:absolute;left:0;top:0;width:140px;height:82px}
.cat-name{position:absolute;left:155px;top:4px;font-size:14px;font-weight:700;color:var(--green);letter-spacing:.3px;white-space:nowrap}
.cat-text{position:absolute;left:155px;top:32px;width:152px;font-size:14px;line-height:18px;color:var(--body-text)}
.cat-more{position:absolute;left:282px;top:95px;color:var(--green);font-size:14px;font-weight:700}
.footer{position:absolute;left:0;top:967px;width:100%;height:201px;background:linear-gradient(var(--footer-top),var(--footer-bottom))}
.foot-col{position:absolute;list-style:none;font-size:12px;color:var(--footer-link)}
.foot-col li{height:25.4px;text-decoration:underline}
.follow{position:absolute;left:772px;top:48px;font-size:15.5px;font-weight:700;color:#8e8e8e;text-decoration:underline}
.social{position:absolute;left:762px;top:105px;display:flex;gap:24px}
.social span{width:42px;height:42px;border-radius:5px;background:linear-gradient(#d9d9d9,#8a8a8a);display:block}
.copyright{position:absolute;left:0;top:1168px;width:100%;height:23px;border-top:1px solid var(--white);background:#000;color:var(--copy);font-size:10.5px;text-align:center;line-height:22px}
</style>
</head>
<body>
<div class="page">
  <header class="header">
    <div class="brand"><span class="brand-mark"></span><span class="brand-name">lotusridge</span></div>
    <div class="phones">Call Now : (555) 318-2740<br>(555) 318-2795</div>
  </header>

  <nav class="nav">
    <span>So Tai Ho</span><span class="sep">|</span>
    <span>Sei Tai Shinpo</span><span class="sep">|</span>
    <span>Acupuncture</span>
    <span class="active">Services</span>
    <span>Biography</span><span class="sep">|</span>
    <span>Nutrition</span><span class="sep">|</span>
    <span>My Journey</span><span class="sep">|</span>
    <span>Contact Us</span>
  </nav>

  <div class="banner" role="img" aria-label="Slideshow photo of people exercising in a gym and with fitness balls"></div>
  <div class="arrow left"><svg width="30" height="30" viewBox="0 0 30 30"><path d="M22 3 L8 15 L22 27" fill="none" stroke="#fff" stroke-width="6"/></svg></div>
  <div class="arrow right"><svg width="30" height="30" viewBox="0 0 30 30" style="left:8px"><path d="M8 3 L22 15 L8 27" fill="none" stroke="#fff" stroke-width="6"/></svg></div>

  <ul class="dropdown">
    <li>Medical Weight Loss</li>
    <li>Hormone Balancing</li>
    <li>Acupuncture</li>
    <li>Chinese Herbal Medicine</li>
    <li>Physical Medicine</li>
    <li>Trigger Point Injections</li>
    <li>Allergy Testing</li>
    <li>Joint Rehabilitation</li>
  </ul>

  <h1 class="intro-title">Change Your Life WITH US!</h1>
  <div class="rule" style="left:56px;top:659px;width:591px"></div>
  <div class="divider"></div>
  <div class="intro-photo" role="img" aria-label="Photo of a smiling woman with an apple holding a bathroom scale"></div>
  <div class="intro-text">
    <p>At Lotus Ridge Wellness Partners the system of acupuncture used is called Seitai Shinpo (which translates into “correct posture acupuncture method”) that uses acupuncture and moxibustion to balance structural distortions by releasing tense areas of contraction along the spine.</p>
    <p>When the structure is properly balanced then the body will heal much quicker.</p>
    <p>Acupuncture has been used to effectively treat numerous health conditions for thousands of years.</p>
  </div>
  <div class="read-more">Read More</div>

  <h2 class="cat-title">Popular Categories</h2>
  <div class="rule" style="left:691px;top:659px;width:288px"></div>

  <div class="cat" style="top:697px">
    <div class="cat-photo" role="img" aria-label="Photo of acupuncture needles being placed" style="background:linear-gradient(90deg,#f3e1d2,#e9c7ad)"></div>
    <div class="cat-name">ACUPUNCTURE</div>
    <div class="cat-text">It has been used to effectively treat numer&shy;ous health conditions</div>
    <div class="cat-more">››</div>
  </div>
  <div class="cat" style="top:831px">
    <div class="cat-photo" role="img" aria-label="Photo of Chinese herbs and a mortar" style="background:linear-gradient(90deg,#6b6a4a,#a88a4a,#7a5a35)"></div>
    <div class="cat-name">NUTRITION AND DIET</div>
    <div class="cat-text">In the healing process, food can be either your best medicine or your</div>
    <div class="cat-more">››</div>
  </div>

  <footer class="footer">
    <ul class="foot-col" style="left:25px;top:34px">
      <li>SO TAI HO</li><li>SEITAI SHINPO</li><li>ACUPUNCTURE</li><li>BIOGRAPHY</li><li>NUTRITION</li><li>MY JOURNEY</li>
    </ul>
    <ul class="foot-col" style="left:255px;top:37px">
      <li>ALLERGIES</li><li>ANXIETY</li><li>ARTHRITIS</li><li>ASTHMA</li><li>ADDICTIONS</li><li>CARPAL TUNNEL SYNDROME</li>
    </ul>
    <ul class="foot-col" style="left:499px;top:34px">
      <li>MENOPAUSE</li><li>MENSTRUAL IRREGULARITIES</li><li>OSTEOARTHRITIS</li><li>PAIN</li><li>PMS</li><li>SCIATICA</li>
    </ul>
    <div class="follow">Follow Us On:</div>
    <div class="social">
      <span role="img" aria-label="Social link"></span>
      <span role="img" aria-label="Social link"></span>
      <span role="img" aria-label="Social link"></span>
      <span role="img" aria-label="Social link"></span>
    </div>
  </footer>
  <div class="copyright">Copyright 2007© Lotus Ridge Wellness Partners — All Rights Reserved</div>
</div>
</body>
</html>
```